Corvana - Waste to Fuel Power Needs A Website

Make website explaining the concept and the team behind the company
Updates

I will be providing A logo and Information about the company upon signed NDA.

Coding

Coded - Design and coding required

Number of Pages Required

5+ page

```html
<!DOCTYPE html>
<html lang="en">
<head>
<meta charset="utf-8">
<title>Corvana - Waste to Fuel Power</title>
<link rel="stylesheet" href="https://fonts.googleapis.com/css2?family=Oswald:wght@500;600&family=Roboto:wght@400;500;700&display=swap">
<style>
:root{
  --green:#7cc242;
  --green-dark:#5fa42d;
  --blue:#1b6fc0;
  --blue-deep:#155aa3;
  --navy:#0d1e3a;
  --ink:#1e1e1e;
  --text:#555;
  --pale:#eef3fb;
  --white:#fff;
}
*{box-sizing:border-box;margin:0;padding:0}
html,body{width:1200px;height:4215px;overflow:hidden}
body{position:relative;background:var(--white);font-family:Roboto,Arial,sans-serif;color:var(--text)}
.abs{position:absolute}
.heading{font-family:Oswald,"Arial Narrow",sans-serif;font-weight:600;color:var(--ink);text-transform:uppercase;letter-spacing:.3px}
.eyebrow{font-family:Oswald,"Arial Narrow",sans-serif;font-weight:500;color:var(--green);text-transform:uppercase;font-size:20px}
.btn{position:absolute;display:flex;align-items:center;justify-content:center;border-radius:30px;background:var(--green);color:var(--white);font-weight:700;font-size:15px;font-family:Roboto,Arial,sans-serif}

/* header */
.topline{top:0;left:0;width:1200px;height:3px;background:var(--green)}
.brand{left:110px;top:40px}
.brand-name{font-family:Oswald,sans-serif;font-weight:600;font-size:50px;line-height:50px;color:var(--blue);text-transform:uppercase;letter-spacing:3px;display:flex;align-items:center;gap:12px}
.brand-dot{width:22px;height:22px;border-radius:50%;background:var(--green)}
.brand-tag{font-family:Oswald,sans-serif;font-weight:600;font-size:18px;color:var(--green);text-transform:uppercase;letter-spacing:1.5px;margin-top:2px}
.nav{top:93px;left:505px;display:flex;gap:42px;font-size:14px;font-weight:500;color:#666;text-transform:uppercase}
.nav .active{color:var(--green)}

/* hero */
.hero-bg{top:144px;left:0;width:1200px;height:683px;background:
  radial-gradient(ellipse at 15% 70%,rgba(230,140,50,.55),transparent 30%),
  radial-gradient(ellipse at 85% 60%,rgba(240,170,70,.45),transparent 30%),
  linear-gradient(180deg,#0b2a52 0%,#13365f 45%,#1b3450 70%,#0c1c33 100%)}
.hero-curve{top:144px;left:0}
.hero-title{top:375px;left:0;width:1200px;text-align:center;color:var(--white);font-size:54px;line-height:60px}
.hero-text{top:502px;left:360px;width:480px;text-align:center;color:var(--white);font-size:18px;line-height:28px}
.hero-mark{top:245px;left:568px;width:64px;height:64px;border-radius:50%;border:4px solid var(--white)}

/* features */
.pill{position:absolute;top:902px;width:306px;height:111px;border-radius:56px;background:var(--pale);display:flex;align-items:center;padding-left:16px;gap:24px;font-size:16px;line-height:24px;color:#555}
.pill.active{background:var(--blue);color:var(--white)}
.pill-icon{width:70px;height:70px;border-radius:50%;background:var(--blue);display:flex;align-items:center;justify-content:center;flex:none}
.pill.active .pill-icon{background:var(--white)}

/* about */
.about-photo{top:1093px;left:111px;width:473px;height:439px;border-radius:24px;box-shadow:0 14px 30px rgba(0,0,0,.25);background:linear-gradient(160deg,#2c6fb0 0%,#5a8cb8 35%,#8a7d6a 60%,#b87566 80%,#6e6a62 100%)}
.about-text{top:1100px;left:651px;width:438px}
.about-text h2{font-size:33px;line-height:40px;margin:8px 0 12px}
.about-lead{font-size:14px;line-height:29px;color:#222}
.about-body{font-size:14px;line-height:29px;text-align:justify;margin-top:24px;color:#666}

/* process */
.center{left:0;width:1200px;text-align:center}
.process-text{top:1715px;left:190px;width:820px;text-align:center;font-size:17px;line-height:31px;color:#666}
.video{top:1853px;left:247px;width:704px;height:427px;border-radius:22px;background:linear-gradient(180deg,#35506a 0%,#4c6b7f 35%,#7fb4b0 70%,#3e6b70 100%);box-shadow:0 10px 26px rgba(0,0,0,.25)}
.play{top:2040px;left:569px;width:62px;height:62px;border-radius:50%;background:var(--white);display:flex;align-items:center;justify-content:center}

/* unique */
.unique-title{top:2360px;left:111px}
.unique-title .eyebrow{color:var(--white)}
.unique-title h2{color:var(--white);font-size:33px;line-height:41px;margin-top:8px}
.quote-btn{top:2536px;left:111px;width:180px;height:44px;background:var(--white);color:var(--green)}
.checks{font-size:16px;color:var(--white)}
.check{position:absolute;display:flex;align-items:center;gap:20px;white-space:nowrap}

/* industries */
.card{position:absolute;top:2848px;width:236px;height:338px;border-radius:14px;background:var(--white);box-shadow:0 4px 16px rgba(0,0,0,.14);overflow:hidden}
.card-img{height:275px}
.card-label{height:63px;display:flex;align-items:center;justify-content:center;font-size:15px;font-weight:500;color:#222}
.card.active{background:var(--green);border:3px solid var(--green)}
.card.active .card-label{color:var(--white)}

/* testimonial */
.quote-text{top:3368px;left:230px;width:740px;text-align:center;font-size:17px;line-height:32px;color:#555}
.quote-strong{top:3532px;font-size:18px;font-weight:500;color:#222}
.author{top:3586px;font-size:18px;color:var(--green)}
.stars{top:3612px;color:#f4a51c;font-size:14px;letter-spacing:2px}
.arrow{position:absolute;top:3666px;width:34px;height:34px;border-radius:50%;display:flex;align-items:center;justify-content:center}

/* footer */
.footer-brand{top:3915px;left:0;width:1200px;display:flex;flex-direction:column;align-items:center}
.footer-brand .brand-name{color:var(--white);font-size:56px;line-height:58px}
.footer-brand .brand-dot{background:var(--white)}
.footer-brand .brand-tag{color:var(--white);font-size:20px}
.footer-nav{top:4032px;left:0;width:1200px;display:flex;justify-content:center;gap:38px;font-size:14px;font-weight:700;color:var(--white);text-transform:uppercase}
.social{position:absolute;top:4079px;width:38px;height:38px;border-radius:50%;background:var(--white)}
.footer-line{top:4138px;left:222px;width:646px;height:1px;background:rgba(255,255,255,.7)}
.gotop{top:4119px;left:866px;width:111px;height:41px;background:var(--white);color:var(--blue);font-size:14px;font-weight:500;gap:8px}
.copyright{top:4164px;font-size:13px;font-weight:700;color:var(--white)}
</style>
</head>
<body>

<!-- header -->
<div class="abs topline"></div>
<div class="abs brand">
  <div class="brand-name"><span class="brand-dot"></span>Corvana</div>
  <div class="brand-tag">Waste to Fuel Power</div>
</div>
<div class="btn" style="top:30px;left:908px;width:180px;height:42px">Partner With Us</div>
<nav class="abs nav">
  <span class="active">Home</span><span>About Us</span><span>Industries We Serve</span><span>Why Us?</span><span>Reviews</span>
</nav>

<!-- hero -->
<div class="abs hero-bg" role="img" aria-label="Industrial refinery skyline at night reflected on water"></div>
<svg class="abs hero-curve" width="1200" height="683" viewBox="0 0 1200 683">
  <path d="M0,440 Q600,880 1200,440 L1200,683 L0,683 Z" fill="#fff"/>
  <path d="M40,470 Q600,830 1160,470 Q600,896 40,470 Z" fill="#1b6fc0"/>
</svg>
<div class="abs hero-mark"></div>
<h1 class="abs heading hero-title">Turning Plastic Waste<br>Into Diesel Energy</h1>
<p class="abs hero-text">Corvana converts non-recyclable plastic into usable diesel fuel, reducing waste while supplying reliable energy for commercial operations.</p>
<div class="btn" style="top:600px;left:511px;width:178px;height:42px">Partner With Us</div>

<!-- features -->
<div class="pill" style="left:116px">
  <span class="pill-icon"><svg width="34" height="34" viewBox="0 0 34 34" fill="none" stroke="#fff" stroke-width="2"><path d="M17 5a9 9 0 0 0-5 16.5V25h10v-3.5A9 9 0 0 0 17 5z"/><path d="M13 29h8"/></svg></span>
  <span>Support circular energy<br>systems</span>
</div>
<div class="pill active" style="left:447px">
  <span class="pill-icon"><svg width="34" height="34" viewBox="0 0 34 34" fill="none" stroke="#1b6fc0" stroke-width="2"><path d="M8 9h18M13 9V6h8v3M10 9l2 20h10l2-20"/></svg></span>
  <span>Create value from<br>waste</span>
</div>
<div class="pill" style="left:778px">
  <span class="pill-icon"><svg width="34" height="34" viewBox="0 0 34 34" fill="none" stroke="#fff" stroke-width="2"><rect x="8" y="6" width="14" height="22" rx="2"/><path d="M22 12l4 3v10a2 2 0 0 1-4 0M11 11h8"/></svg></span>
  <span>Reduce plastic waste &amp;<br>Produce fuel</span>
</div>

<!-- about -->
<div class="abs about-photo" role="img" aria-label="Plastic waste moving up a conveyor at a sorting plant"></div>
<div class="abs about-text">
  <div class="eyebrow">Who We Are</div>
  <h2 class="heading">The World Has A Plastic<br>Waste Problem</h2>
  <p class="about-lead">At the same time, industries around the world depend on diesel fuel for logistics, agriculture, and manufacturing.</p>
  <p class="about-body">Sed ut perspiciatis unde omnis iste natus error sit voluptatem accusantium doloremque laudantium, totam rem aperiam, eaque ipsa quae ab illo inventore veritatis et quasi architecto beatae vitae dicta sunt explicabo. Nemo enim ipsam voluptatem quia voluptas sit aspernatur</p>
</div>
<div class="btn" style="top:1477px;left:651px;width:138px;height:42px;font-size:14px">Explore More</div>

<!-- process -->
<div class="abs eyebrow center" style="top:1628px">How It Works</div>
<h2 class="abs heading center" style="top:1664px;font-size:33px">Plastic To Diesel Energy</h2>
<p class="abs process-text">Sed ut perspiciatis unde omnis iste natus error sit voluptatem accusantium doloremque laudantium, totam rem aperiam, eaque ipsa quae ab illo inventore veritatis et quasi architecto beatae vitae dicta sunt explicabo. Nemo enim ipsam voluptatem</p>

<svg class="abs" style="top:2000px;left:0" width="1200" height="647" viewBox="0 2000 1200 647" role="img" aria-label="Green grass field background">
  <defs>
    <linearGradient id="grass" x1="0" y1="0" x2="0" y2="1">
      <stop offset="0" stop-color="#7dc443"/><stop offset="1" stop-color="#68b335"/>
    </linearGradient>
  </defs>
  <path d="M60,2172 C280,2062 500,2012 600,2012 C700,2012 920,2062 1140,2172 C920,2078 700,2040 600,2040 C500,2040 280,2078 60,2172 Z" fill="#1b6fc0"/>
  <path d="M0,2222 C250,2080 500,2030 600,2030 C700,2030 950,2080 1200,2222 L1200,2647 L0,2647 Z" fill="url(#grass)"/>
</svg>
<div class="abs video" role="img" aria-label="Plastic bottles on a recycling conveyor line"></div>
<div class="abs play"><svg width="26" height="26" viewBox="0 0 26 26"><circle cx="13" cy="13" r="13" fill="#7cc242"/><path d="M10 7l9 6-9 6z" fill="#fff"/></svg></div>

<!-- unique -->
<div class="abs unique-title">
  <div class="eyebrow">What Makes Us Unique</div>
  <h2 class="heading">Why Commercial<br>Fuel Buyers Work<br>With Corvana</h2>
</div>
<div class="btn quote-btn">Request a Quote</div>
<div class="checks">
  <div class="check" style="top:2360px;left:470px"><svg width="16" height="16" viewBox="0 0 16 16"><circle cx="8" cy="8" r="8" fill="#fff"/><path d="M4.5 8.2l2.3 2.3 4.7-4.8" fill="none" stroke="#7cc242" stroke-width="2"/></svg>Reduce plastic waste</div>
  <div class="check" style="top:2404px;left:470px"><svg width="16" height="16" viewBox="0 0 16 16"><circle cx="8" cy="8" r="8" fill="#fff"/><path d="M4.5 8.2l2.3 2.3 4.7-4.8" fill="none" stroke="#7cc242" stroke-width="2"/></svg>Produce usable fuel</div>
  <div class="check" style="top:2448px;left:470px"><svg width="16" height="16" viewBox="0 0 16 16"><circle cx="8" cy="8" r="8" fill="#fff"/><path d="M4.5 8.2l2.3 2.3 4.7-4.8" fill="none" stroke="#7cc242" stroke-width="2"/></svg>Support circular energy systems</div>
  <div class="check" style="top:2492px;left:470px"><svg width="16" height="16" viewBox="0 0 16 16"><circle cx="8" cy="8" r="8" fill="#fff"/><path d="M4.5 8.2l2.3 2.3 4.7-4.8" fill="none" stroke="#7cc242" stroke-width="2"/></svg>Create value from waste</div>
  <div class="check" style="top:2536px;left:470px"><svg width="16" height="16" viewBox="0 0 16 16"><circle cx="8" cy="8" r="8" fill="#fff"/><path d="M4.5 8.2l2.3 2.3 4.7-4.8" fill="none" stroke="#7cc242" stroke-width="2"/></svg>Reliable Fuel Supply</div>
  <div class="check" style="top:2360px;left:820px"><svg width="16" height="16" viewBox="0 0 16 16"><circle cx="8" cy="8" r="8" fill="#fff"/><path d="M4.5 8.2l2.3 2.3 4.7-4.8" fill="none" stroke="#7cc242" stroke-width="2"/></svg>Environmental Responsibility</div>
  <div class="check" style="top:2404px;left:820px"><svg width="16" height="16" viewBox="0 0 16 16"><circle cx="8" cy="8" r="8" fill="#fff"/><path d="M4.5 8.2l2.3 2.3 4.7-4.8" fill="none" stroke="#7cc242" stroke-width="2"/></svg>Scalable Infrastructure</div>
  <div class="check" style="top:2448px;left:820px"><svg width="16" height="16" viewBox="0 0 16 16"><circle cx="8" cy="8" r="8" fill="#fff"/><path d="M4.5 8.2l2.3 2.3 4.7-4.8" fill="none" stroke="#7cc242" stroke-width="2"/></svg>Circular Economy</div>
</div>

<!-- industries -->
<div class="abs eyebrow center" style="top:2728px">Industries We Serve</div>
<h2 class="abs heading center" style="top:2764px;font-size:33px">Fuel For Commercial Operations</h2>
<div class="card" style="left:111px"><div class="card-img" role="img" aria-label="Forklift loading boxes into a truck" style="background:linear-gradient(160deg,#c9c2b4,#8a7d68 55%,#e3a23a 85%,#3b3b3b)"></div><div class="card-label">Transportation &amp; Trucking</div></div>
<div class="card active" style="left:358px"><div class="card-img" role="img" aria-label="Building under construction with a crane at sunset" style="background:linear-gradient(180deg,#7b8fa8,#c79c63 55%,#6a4a2e)"></div><div class="card-label">Construction</div></div>
<div class="card" style="left:606px"><div class="card-img" role="img" aria-label="Irrigation sprinklers over crop rows" style="background:linear-gradient(180deg,#4f7a5a,#5f9a3e 55%,#2f5a24)"></div><div class="card-label">Agriculture</div></div>
<div class="card" style="left:853px"><div class="card-img" role="img" aria-label="Container port seen from above at night" style="background:linear-gradient(135deg,#1c3f77,#3c5f96 45%,#c9703c 65%,#1a2a4a)"></div><div class="card-label">Shipping &amp; Logistics</div></div>

<!-- testimonial -->
<svg class="abs" style="top:3292px;left:566px" width="68" height="48" viewBox="0 0 68 48"><path d="M4 20a14 14 0 1 1 22 11c-3 8-9 14-18 17 5-5 7-9 7-13A14 14 0 0 1 4 20zM38 20a14 14 0 1 1 22 11c-3 8-9 14-18 17 5-5 7-9 7-13A14 14 0 0 1 38 20z" fill="#1b6fc0"/></svg>
<p class="abs quote-text">Sed ut perspiciatis unde omnis iste natus error sit voluptatem accusantium doloremque laudantium, totam rem aperiam, eaque ipsa quae ab illo inventore veritatis et quasi architecto beatae vitae dicta sunt explicabo. Nemo enim ipsam voluptatem quia voluptas sit aspernatur aut odit aut fugit, sed quia consequuntur magni dolores</p>
<div class="abs center quote-strong">Neque porro quisquam est, qui dolorem ipsum</div>
<div class="abs center author">Mara Ellison</div>
<div class="abs center stars">★★★★★</div>
<div class="arrow" style="left:561px;background:#e3f1d6"><svg width="12" height="12" viewBox="0 0 12 12" fill="none" stroke="#7cc242" stroke-width="2"><path d="M6 2L2 6l4 4M10 2L6 6l4 4"/></svg></div>
<div class="arrow" style="left:605px;background:var(--green)"><svg width="12" height="12" viewBox="0 0 12 12" fill="none" stroke="#fff" stroke-width="2"><path d="M2 2l4 4-4 4M6 2l4 4-4 4"/></svg></div>

<!-- footer -->
<svg class="abs" style="top:3760px;left:0" width="1200" height="455" viewBox="0 3760 1200 455" role="img" aria-label="Blue footer backdrop with faint industrial scene">
  <defs>
    <linearGradient id="foot" x1="0" y1="0" x2="0" y2="1">
      <stop offset="0" stop-color="#1d72c4"/><stop offset="1" stop-color="#1760ad"/>
    </linearGradient>
  </defs>
  <path d="M50,3960 Q600,3602 1150,3960 Q600,3680 50,3960 Z" fill="#7cc242"/>
  <path d="M0,3980 Q600,3664 1200,3980 L1200,4215 L0,4215 Z" fill="url(#foot)"/>
</svg>
<div class="abs footer-brand">
  <div class="brand-name"><span class="brand-dot"></span>Corvana</div>
  <div class="brand-tag">Waste to Fuel Power</div>
</div>
<nav class="abs footer-nav"><span>Home</span><span>About Us</span><span>Our Services</span><span>Testimonials</span><span>Why Choose Us</span><span>Contact Us</span></nav>
<span class="social" style="left:534px"></span>
<span class="social" style="left:581px"></span>
<span class="social" style="left:628px"></span>
<div class="abs footer-line"></div>
<div class="btn gotop"><svg width="12" height="12" viewBox="0 0 12 12" fill="none" stroke="#1b6fc0" stroke-width="2.2"><path d="M2 8l4-4 4 4"/></svg>GO TOP</div>
<div class="abs center copyright">(C) COPYRIGHT 2026 | ALL RIGHTS RESERVED</div>

</body>
</html>
```